Road Construction Company needs business cards

We would like a new business card designed for our business.

We're a road construction company based in Qld, Australia.

Can the business card please have the following information on it.

Name: Warren Halbeck
Position: General Manager
Phone: 0472 915 348
Email: Warren.halbeck@tovrin.com.au
Address: 87 Marrow Ave, Pendlebay, QLD, 4023
Website: www.tovrin.com.au

Visually we'd like the card to be professional and simple.

Attached is our logo.

Our website is www.tovrin.com.au

Target Market(s)

Men aged 25-60

Contact Information for Business Card

As listed in project description

Font styles to use
Serif

Requirements
Must have
• Large logo on back of card

```html
<!DOCTYPE html>
<html lang="en">
<head>
<meta charset="utf-8">
<title>Tovrin Road Construction – Business Card</title>
<link rel="stylesheet" href="https://fonts.googleapis.com/css2?family=Nunito+Sans:wght@700;800&display=swap">
<style>
  :root {
    --stage-top: #666666;
    --stage-bottom: #36373d;
    --card-blue: #0c57a3;
    --accent-line: #3d9fe2;
    --ink-blue: #0d56a3;
    --icon-blue: #0e4f98;
    --card-white: #ffffff;
    --logo-white: #ffffff;
  }
  * { margin: 0; padding: 0; box-sizing: border-box; }
  html, body { width: 1200px; height: 2250px; overflow: hidden; }
  body {
    position: relative;
    font-family: "Nunito Sans", Arial, sans-serif;
    background: var(--stage-bottom);
  }
  .stage-top {
    position: absolute; left: 0; top: 0;
    width: 1200px; height: 1325px;
    background: var(--stage-top);
  }
  .card { position: absolute; }
  .card-back {
    left: 86px; top: 38px; width: 1059px; height: 602px;
    background: var(--card-blue);
  }
  .rule {
    position: absolute; top: 309px; height: 4px;
    background: var(--accent-line);
  }
  .rule-left { left: 0; width: 259px; }
  .rule-right { right: 0; width: 259px; }
  .brand {
    position: absolute; left: 0; right: 0; top: 270px;
    text-align: center;
    color: var(--logo-white);
    font-weight: 800;
    font-size: 76px;
    line-height: 80px;
    letter-spacing: 4px;
  }
  .card-front {
    left: 90px; top: 675px; width: 1059px; height: 602px;
    background: var(--card-white);
  }
  .identity {
    position: absolute; left: 0; width: 484px; top: 270px;
    text-align: center; color: var(--ink-blue);
  }
  .identity-name {
    font-weight: 800; font-size: 28px; letter-spacing: 0.5px;
    text-transform: uppercase;
  }
  .identity-role {
    margin-top: 10px;
    font-weight: 800; font-size: 13px; letter-spacing: 1.5px;
    text-transform: uppercase;
  }
  .divider {
    position: absolute; left: 420px; top: 120px; width: 90px; height: 390px;
    background: linear-gradient(90deg, rgba(255,255,255,0) 0%, rgba(0,0,0,0.07) 100%);
    -webkit-mask: linear-gradient(180deg, transparent, #000 30%, #000 70%, transparent);
    mask: linear-gradient(180deg, transparent, #000 30%, #000 70%, transparent);
  }
  .contact-list { list-style: none; position: absolute; left: 472px; top: 0; }
  .contact-item {
    position: absolute; left: 0; display: flex; align-items: center;
    white-space: nowrap;
    color: var(--ink-blue);
    font-weight: 800; font-size: 19px; letter-spacing: 1.6px;
  }
  .contact-item svg { width: 32px; height: 32px; margin-right: 20px; flex: none; }
  .contact-email { top: 167px; }
  .contact-phone { top: 241px; }
  .contact-address { top: 307px; }
  .contact-web { top: 386px; }
</style>
</head>
<body>
  <div class="stage-top"></div>

  <section class="card card-back" aria-label="Card back">
    <div class="rule rule-left"></div>
    <div class="rule rule-right"></div>
    <div class="brand">TOVRIN</div>
  </section>

  <section class="card card-front" aria-label="Card front">
    <div class="identity">
      <div class="identity-name">Warren Halbeck</div>
      <div class="identity-role">General Manager</div>
    </div>
    <div class="divider"></div>
    <ul class="contact-list">
      <li class="contact-item contact-email">
        <svg viewBox="0 0 32 32" aria-hidden="true"><circle cx="16" cy="16" r="16" fill="var(--icon-blue)"/><rect x="8.5" y="10.5" width="15" height="11" rx="1" fill="none" stroke="#fff" stroke-width="1.8"/><path d="M9 11.5 L16 17 L23 11.5" fill="none" stroke="#fff" stroke-width="1.8"/></svg>
        Warren.halbeck@tovrin.com.au
      </li>
      <li class="contact-item contact-phone">
        <svg viewBox="0 0 32 32" aria-hidden="true"><circle cx="16" cy="16" r="16" fill="var(--icon-blue)"/><path d="M11 8.5c1-.6 2-.4 2.5.5l1.3 2.6c.4.8.2 1.6-.5 2.1l-1 .7c.8 2 2.3 3.6 4.3 4.5l.8-1c.5-.7 1.4-.9 2.1-.5l2.5 1.4c.9.5 1.1 1.6.5 2.5l-1 1.3c-.8 1-2.2 1.4-3.4.9-4.4-1.8-7.6-5-9.3-9.4-.4-1.2 0-2.6 1.2-3.6z" fill="#fff"/></svg>
        0472 915 348
      </li>
      <li class="contact-item contact-address">
        <svg viewBox="0 0 32 32" aria-hidden="true"><circle cx="16" cy="16" r="16" fill="var(--icon-blue)"/><path d="M16 8 L25 16 H22.5 V24 H18 V19 H14 V24 H9.5 V16 H7 Z" fill="#fff"/></svg>
        87 Marrow Ave, Pendlebay, QLD, 4023
      </li>
      <li class="contact-item contact-web">
        <svg viewBox="0 0 32 32" aria-hidden="true"><circle cx="16" cy="16" r="16" fill="var(--icon-blue)"/><circle cx="16" cy="16" r="8" fill="none" stroke="#fff" stroke-width="1.8"/><ellipse cx="16" cy="16" rx="3.5" ry="8" fill="none" stroke="#fff" stroke-width="1.5"/><path d="M8 16 H24" stroke="#fff" stroke-width="1.5"/></svg>
        www.tovrin.com.au
      </li>
    </ul>
  </section>
</body>
</html>
```